Business Card Design 2018 Kestrel Machining

Hello,

We need a business card design to reflect our new website we just had designed ( http://www.kestrelmachining.ca/)

We are a growing machine shop looking to grow our clientele and are hoping to update our current business card design to match our website and industry

The colours and design of our website should match to achieve what we are looking for.

I have attached a few images for reference as well as our logo and ISO 9000 needs to be apparent on the card as well

Please let me know what you have :)
Please copy marla@kestrelmachining.ca on all communication regarding this project

Thanks !!!

Industry/Entity Type

Business

Contact Information for Business Card

Company Name, employee name and title and contact details

Colors
f78f20
ffffff
00a990

Requirements
Must have
• Our logo, Iso 9000 same colours as our website http://www.kestrelmachining.ca/

```html
<!DOCTYPE html>
<html lang="en">
<head>
<meta charset="utf-8">
<title>Kestrel Machining – Business Card</title>
<link rel="stylesheet" href="https://fonts.googleapis.com/css2?family=Roboto:wght@400;500;700;900&display=swap">
<style>
  :root {
    --backdrop: #7a5a44;
    --card-white: #f4f4f4;
    --teal: #1f9ea6;
    --teal-light: #3fc4d0;
    --teal-dark: #139099;
    --ink: #111111;
    --text-grey: #555555;
    --divider: #b5b5b5;
  }
  * { margin: 0; padding: 0; box-sizing: border-box; }
  html, body { width: 1200px; height: 960px; overflow: hidden; }
  body {
    position: relative;
    background: var(--backdrop);
    font-family: "Roboto", Arial, sans-serif;
  }
  .card {
    position: absolute;
    width: 600px;
    height: 343px;
    box-shadow: 0 3px 8px rgba(0,0,0,0.45);
  }
  .card-front { left: 314px; top: 113px; background: var(--card-white); }
  .card-back {
    left: 311px; top: 472px;
    background: radial-gradient(ellipse 60% 65% at 50% 45%, var(--teal-light) 0%, #2bb0bc 45%, var(--teal-dark) 100%);
  }

  .brand {
    position: absolute;
    display: flex;
    align-items: center;
    color: var(--ink);
    font-weight: 900;
    text-transform: uppercase;
    white-space: nowrap;
  }
  .brand-mark { background: var(--teal); flex: none; }
  .card-front .brand { left: 58px; top: 154px; gap: 8px; font-size: 17px; line-height: 32px; }
  .card-front .brand-mark { width: 32px; height: 32px; }
  .card-back .brand {
    left: 50%; top: 150px; transform: translateX(-50%);
    gap: 10px; font-size: 24px; line-height: 44px;
  }
  .card-back .brand-mark { width: 44px; height: 44px; background: var(--ink); }

  .divider {
    position: absolute;
    left: 328px; top: 72px;
    width: 2px; height: 200px;
    background: linear-gradient(to bottom, transparent, var(--divider) 20%, var(--divider) 80%, transparent);
  }

  .contact { position: absolute; left: 357px; top: 72px; color: var(--text-grey); }
  .contact-name { color: var(--teal); font-size: 21px; font-weight: 500; line-height: 24px; }
  .contact-title { color: var(--ink); font-size: 15px; font-weight: 500; line-height: 20px; margin-bottom: 10px; }
  .contact-address { font-size: 14.5px; line-height: 19px; margin-bottom: 10px; }
  .contact-list { list-style: none; font-size: 14.5px; }
  .contact-list li { display: flex; align-items: center; height: 19px; }
  .contact-list svg { width: 13px; height: 13px; margin-right: 10px; flex: none; fill: var(--teal); }

  .badges { position: absolute; right: 28px; top: 25px; display: flex; gap: 16px; }
  .badge { height: 22px; background: var(--ink); }
  .badge-iso { width: 80px; }
  .badge-partner { width: 78px; }

  .back-web {
    position: absolute; left: 0; right: 0; top: 287px;
    text-align: center;
    font-size: 15px; letter-spacing: 5px;
    color: var(--ink);
  }
</style>
</head>
<body>
  <section class="card card-front">
    <div class="brand"><span class="brand-mark"></span>Kestrel Machining</div>
    <div class="divider"></div>
    <div class="contact">
      <p class="contact-name">OWEN HARTLEY</p>
      <p class="contact-title">CEO/FOUNDER</p>
      <p class="contact-address">2140 Birchwood Road<br>Hamilton, Ontario L8N 2T4</p>
      <ul class="contact-list">
        <li><svg viewBox="0 0 16 16" aria-hidden="true"><path d="M3 1l3 3-1.5 2c1 2 3 4 5 5L11.5 9.5l3 3L13 15C7 15 1 9 1 3z"/></svg>905 412 7781</li>
        <li><svg viewBox="0 0 16 16" aria-hidden="true"><path d="M4 0h8v16H4zM5.5 2v10h5V2z"/></svg>905 618 3390</li>
        <li><svg viewBox="0 0 16 16" aria-hidden="true"><path d="M4 1h8v4H4zM1 6h14v6h-2v3H3v-3H1zM5 10v3h6v-3z"/></svg>905 412 7782</li>
        <li><svg viewBox="0 0 16 16" aria-hidden="true"><path d="M1 3h14v10H1zM2.5 4.5L8 9l5.5-4.5z"/></svg>marla@kestrelmachining.ca</li>
        <li><svg viewBox="0 0 16 16" aria-hidden="true"><circle cx="8" cy="8" r="7"/></svg>www.kestrelmachining.ca</li>
      </ul>
    </div>
  </section>

  <section class="card card-back">
    <div class="badges">
      <span class="badge badge-iso" role="img" aria-label="ISO 9001 certification badge"></span>
      <span class="badge badge-partner" role="img" aria-label="Partner badge"></span>
    </div>
    <div class="brand"><span class="brand-mark"></span>Kestrel Machining</div>
    <p class="back-web">www.kestrelmachining.ca</p>
  </section>
</body>
</html>
```